Visitenkarten/Briefpaier/Kassenkassenbelege für Juwelier
Zielgruppe
Mittelständischer Juwelier mit zwei Filialen. Klassischer Schmuck, Uhren und Modeschmuck
Aufgabenstellung
Es müssen für zwei Geschäfte Visitenkarten, Briefpapier (A4) und Kassenkassenbelege (A6) erstellt werden. Logo und Typo im Anhang. Ein Farbkonzept besteht noch nicht. Die Idee geht in Richtung Bordeaux-Rot.
Generell:
(1) Sieht erstmal nach viel Beschreibung aus, bitte nicht entmutigen lassen, sind zu 90% nur austauschbare Inhalts-/Kontaktdaten.
(2) Für meine Zwecke reicht es vollkommen aus, wenn bei den Vorschlägen zur Arbeitsersparnis erstmal nur mit einer Adresse gearbeitet wird. Wenn ich dann den zutreffenden Designvorschlag gefunden habe, können wir die zweite Adresse in dem ersten Format umsetzen. Ich denke das spart Zeit und Nerven.
(3) Bitte Angaben wie "Tel.:" oder "USt.- ID:" nicht wörtlich nehmen, es soll dabei klar sein worum es geht; wenn "Telefon" ausgeschrieben besser aussieht, bitte in der optisch ansprechenderen Form verwenden.
(4) Bei Fragen, bitte fragen!
(5) Viel Spass bei dem Projekt - Ich freu' mich auf die Vorschläge!
Visitenkarten(1):
Juwelier Brenneck GmbH
www.juwelier-brenneck-beispiel.de
Visitenkarten(2):
Visitenkarten(generell):
(1) Die einzelnen Daten können durch Hervorhebungen wie Adresse, Kontakt, Online/Internet unterteilt bzw. hervorgehoben werden.
(2) Die Visitenkarten sollen farbig gedruckt werden; geplant ist weiß als Hintergrund ist aber nicht zwingend bei einer guten anderen Idee
Briefpapier:
(1)Absender im Adressfeld für DIN-lang Briefumschläge mit Fenster:
(2)Informationen im Footer/Seitenbereich:
Juwelier Brenneck Gmb..

```html
<!DOCTYPE html>
<html lang="de">
<head>
<meta charset="utf-8">
<title>Juwelier Brenneck – Geschäftsausstattung</title>
<link rel="stylesheet" href="https://fonts.googleapis.com/css2?family=Source+Sans+3:wght@400;600&display=swap">
<style>
:root{
  --mauve-top:#a6969c;
  --mauve-bottom:#86747a;
  --mauve:#9a848b;
  --mauve-text:#a08990;
  --grey:#7d7d7d;
  --grey-text:#8b8b8b;
  --ink:#2a2a2a;
  --paper-top:#f7f7f7;
  --paper-bottom:#c9c9c9;
  --white:#ffffff;
}
*{box-sizing:border-box;margin:0;padding:0}
html,body{width:872px;height:1200px;overflow:hidden}
body{font-family:"Source Sans 3",sans-serif;background:linear-gradient(180deg,var(--mauve-top),var(--mauve-bottom));position:relative}
.abs{position:absolute}
.brand-square{position:absolute;left:50%;transform:translateX(-50%)}
.brand-name{position:absolute;left:0;right:0;text-align:center;font-weight:400;letter-spacing:.02em;white-space:nowrap}
.brand-rule{position:absolute;left:50%;transform:translateX(-50%);height:1px}

/* poster header */
.hero .brand-square{top:32px;width:49px;height:88px;background:var(--white)}
.hero .brand-name{top:136px;font-size:25px;color:var(--grey);line-height:1}
.hero .brand-rule{top:180px;width:246px;background:var(--grey)}

.sheet{position:absolute;background:linear-gradient(180deg,var(--paper-top),var(--paper-bottom))}
.tab{position:absolute;bottom:0;left:50%;transform:translateX(-50%);width:17px;height:8px;background:var(--grey)}

/* receipt */
.receipt{left:100px;top:289px;width:218px;height:320px;background:linear-gradient(180deg,#fafafa,#e4e4e4)}
.receipt .brand-square{top:8px;width:22px;height:32px;background:var(--mauve)}
.receipt .brand-name{top:45px;font-size:9px;color:var(--grey)}
.receipt .brand-rule{top:62px;width:90px;background:var(--grey)}
.ruled{position:absolute;left:26px;right:26px;top:102px}
.ruled span{display:block;height:12.9px;border-top:1px solid #bdbdbd}
.receipt-note{position:absolute;top:247px;left:0;right:0;text-align:center;font-size:5px;line-height:7px;color:var(--mauve-text)}
.receipt-foot{position:absolute;top:282px;left:0;right:0;text-align:center;font-size:4.6px;line-height:7px;color:var(--mauve-text)}

/* business cards */
.card{position:absolute;width:177px;height:119px}
.card-front{left:336px;top:289px;background:linear-gradient(180deg,#fafafa,#e2e2e2)}
.card-front .brand-square{top:9px;width:22px;height:38px;background:var(--grey)}
.card-front .brand-name{top:53px;font-size:11px;color:var(--grey)}
.card-front .brand-rule{top:75px;width:110px;background:var(--grey)}
.card-dark{left:529px;top:289px;border:1px solid #e8e0e2;background:transparent}
.card-dark .brand-square{top:9px;width:22px;height:38px;background:var(--white)}
.card-dark .brand-name{top:53px;font-size:11px;color:var(--grey)}
.card-dark .brand-rule{top:75px;width:110px;background:#c9bcc0}
.card-dark .tab{background:var(--grey)}
.card-back{left:140px;background:linear-gradient(180deg,#f8f8f8,#e0e0e0)}
.card-back .brand-square{top:9px;width:22px;height:38px;background:var(--grey)}
.card-back.alt .brand-square{background:var(--mauve)}
.card-back-1{top:625px}
.card-back-2{top:760px}
.card-contact{position:absolute;top:58px;left:0;right:0;text-align:center;font-size:4.6px;line-height:8px;color:var(--mauve-text)}
.card-contact strong{font-weight:600}

/* letter */
.letter{left:336px;top:425px;width:437px;height:643px}
.letter .brand-square{top:13px;width:22px;height:42px;background:var(--mauve)}
.letter .brand-name{top:61px;font-size:12px;color:var(--grey)}
.letter .brand-rule{top:80px;width:120px;background:var(--grey)}
.sender{position:absolute;top:108px;left:50px;font-size:4.4px;color:var(--grey-text)}
.contact-block{position:absolute;top:108px;left:257px;font-size:4.4px;line-height:7px;color:var(--mauve-text)}
.recipient{position:absolute;top:127px;left:50px;font-size:6.4px;line-height:9px;color:var(--ink)}
.recipient strong{font-weight:600}
.recipient .city{margin-top:9px}
.date{position:absolute;top:220px;right:49px;font-size:6.4px;color:var(--ink)}
.subject{position:absolute;top:233px;left:0;right:0;text-align:center;font-size:6.6px;font-weight:600;color:var(--ink)}
.body{position:absolute;top:265px;left:50px;width:340px;font-size:6.3px;line-height:12.4px;color:var(--ink)}
.body p{margin-bottom:12.4px}
.letter-foot{position:absolute;top:598px;left:0;right:0;text-align:center;font-size:4.2px;line-height:7px;color:var(--grey-text)}
</style>
</head>
<body>

<header class="hero">
  <div class="brand-square"></div>
  <div class="brand-name">JUWELIER BRENNECK</div>
  <div class="brand-rule"></div>
</header>

<section class="sheet receipt" aria-label="Kassenbeleg A6">
  <div class="brand-square"></div>
  <div class="brand-name">JUWELIER BRENNECK</div>
  <div class="brand-rule"></div>
  <div class="ruled"><span></span><span></span><span></span><span></span><span></span><span></span><span></span><span></span><span></span><span></span><span></span></div>
  <p class="receipt-note">Bei Umtausch oder Reklamation bitte Beleg vorlegen.<br>Barauszahlung ganz oder teilweise ausgeschlossen.</p>
  <p class="receipt-foot">JUWELIER BRENNECK GmbH<br>Goldschmiedgasse 12 in 45000 Beispielstadt &nbsp;TEL 0000-123456 &nbsp;FAX 0000-123457<br>info@juwelier-brenneck-beispiel.de &nbsp;www.juwelier-brenneck-beispiel.de</p>
  <div class="tab"></div>
</section>

<section class="card card-front" aria-label="Visitenkarte Vorderseite hell">
  <div class="brand-square"></div>
  <div class="brand-name">JUWELIER BRENNECK</div>
  <div class="brand-rule"></div>
  <div class="tab"></div>
</section>

<section class="card card-dark" aria-label="Visitenkarte Vorderseite farbig">
  <div class="brand-square"></div>
  <div class="brand-name">JUWELIER BRENNECK</div>
  <div class="brand-rule"></div>
  <div class="tab"></div>
</section>

<section class="card card-back card-back-1" aria-label="Visitenkarte Rückseite">
  <div class="brand-square"></div>
  <p class="card-contact"><strong>JUWELIER BRENNECK GmbH</strong><br>Goldschmiedgasse 12 in 45000 Beispielstadt<br><strong>TEL</strong> 0000-123456 &nbsp;<strong>FAX</strong> 0000-123457 &nbsp;<strong>info@juwelier-brenneck-beispiel.de</strong><br><strong>www.juwelier-brenneck-beispiel.de</strong></p>
  <div class="tab"></div>
</section>

<section class="card card-back alt card-back-2" aria-label="Visitenkarte Rückseite Variante">
  <div class="brand-square"></div>
  <p class="card-contact"><strong>JUWELIER BRENNECK GmbH</strong><br>Goldschmiedgasse 12 in 45000 Beispielstadt<br><strong>TEL</strong> 0000-123456 &nbsp;<strong>FAX</strong> 0000-123457 &nbsp;<strong>info@juwelier-brenneck-beispiel.de</strong><br><strong>www.juwelier-brenneck-beispiel.de</strong></p>
  <div class="tab"></div>
</section>

<section class="sheet letter" aria-label="Briefpapier A4">
  <div class="brand-square"></div>
  <div class="brand-name">JUWELIER BRENNECK</div>
  <div class="brand-rule"></div>
  <p class="sender">JUWELIER BRENNECK GmbH &nbsp;Goldschmiedgasse 12 in 45000 Beispielstadt</p>
  <p class="contact-block">TEL 0000-123456 &nbsp;FAX 0000-123457 &nbsp;info@juwelier-brenneck-beispiel.de<br>www.juwelier-brenneck-beispiel.de</p>
  <div class="recipient">
    <p>Frau</p>
    <p><strong>Henriette Saphir</strong></p>
    <p>Rubinweg 38</p>
    <p class="city">45000 Beispielstadt</p>
  </div>
  <p class="date">Beispielstadt, den 03. 05. 2014</p>
  <p class="subject">DIAMANTSTAUB AM HORIZONT</p>
  <div class="body">
    <p>Sehr geehrte Frau Saphir,</p>
    <p>hier schreibe ich einen Blindtext dahin: Diamanten, die groß genug für die Schmuckproduktion sind, bilden sich nur im Erdmantel unter hohen Drücken und Temperaturen, typischerweise in Tiefen zwischen 150 bis 660 Kilometern[4] und bei Temperaturen von 1200 bis 1400 °C. Diamant-Muttergesteine im Erdmantel sind Peridotit und Eklogit. Letzterer kann versenkte ozeanische Kruste repräsentieren.</p>
    <p>Die jeweilige Transportdauer aus der Tiefe wird auf wenige Stunden geschätzt, sodass aufgrund der Schnelligkeit keine Phasenumwandlung zu Graphit stattfindet. Die letzte Phase der Eruption erfolgt mit Überschallgeschwindigkeit. Diamanten sind Fremd- oder Xenokristalle in Kimberlit und Lamproit und in diesen Magmen chemisch nicht stabil (metastabil).</p>
    <p>So kann man an natürlichen Diamanten immer Auflösungserscheinungen beobachten. Von ihren Vorkommen in Pipes können die Diamantkristalle durch natürliche Verwitterungsprozesse, bei denen sie aufgrund ihrer Härte intakt bleiben, abtransportiert und in Sedimentgesteinen angereichert werden, die heute eine der Hauptquellen dieses Minerals darstellen.</p>
    <p>Mit den allerbesten Grüßen</p>
    <p>Clara Topas</p>
  </div>
  <p class="letter-foot">Juwelier Brenneck GmbH &nbsp;Goldschmiedgasse 12 in 45000 Beispielstadt<br>Geschäftsführer Greta Brenneck &nbsp;Amtsgericht Beispielstadt HRB 00000 &nbsp;Steuernummer 000/0000/0000 &nbsp;USt.- ID DE 000000000<br>Beispielbank AG &nbsp;IBAN DE00 0000 0000 0000 0000 00 &nbsp;BIC BSPL DE 00</p>
  <div class="tab"></div>
</section>

</body>
</html>
```